redesign of my existing custom website into Wordpress based website

I need someone to redesign my current website into something more classy, simplistic, modern and on trend. I would like it set up on Wordpress in a way thats easy for me to make my own additions to blogs/price changes and promotion banners. I will also need a page that is password protected so members can login and have access to all my training videos and resources.
website is www.tidewellmamas.com.au

Target Market(s)

new mums

Industry/Entity Type

Fitness

Coding

Coded - Design and coding required

Number of Pages Required

5+ page

Colors
33a6d7

Requirements
Must have
• chic, modern, stylish and simplistic.
• a call to action above the page fold
• mobile friendly conversion
• a pop up message as soon as someone enters my sight offering my free report
• a members page that is password protected containing 3 youtube videos and 6 pdf attachments as resources
• a home page
• a contact us page
• an about us page
• a blog page
• a store page
Nice to have
• some examples of my peers websites that I like:
• www.norapellwick.com
• https://www.9qlr.com
• https://41bytedgarth.com
Should not have
• anything gimmicky

```html
<!DOCTYPE html>
<html lang="en">
<head>
<meta charset="utf-8">
<title>Tidewell Mamas – Home Fitness</title>
<link href="https://fonts.googleapis.com/css2?family=Jost:wght@400;500&family=Open+Sans:wght@400;600&display=swap" rel="stylesheet">
<style>
:root{
  --blue:#33a6d7;
  --blue-deep:#1f86bd;
  --pink:#d6187a;
  --ink:#2b2b2b;
  --body:#555;
  --muted:#8a8a8a;
  --page:#f7f7f7;
  --footer:#efefef;
  --dark:#1c1c1e;
  --white:#fff;
}
*{box-sizing:border-box;margin:0;padding:0}
html,body{width:1200px;height:2932px;overflow:hidden}
body{position:relative;background:var(--page);font-family:"Open Sans",sans-serif;color:var(--body)}
h1,h2,h3,h4{font-weight:400}
.heading{font-family:"Jost",sans-serif;font-weight:400;text-transform:uppercase}

/* header */
.site-header{position:absolute;left:0;top:0;width:1200px;height:92px;background:var(--white)}
.brand-badge{position:absolute;left:96px;top:10px;width:142px;height:142px;border-radius:50%;background:var(--white);box-shadow:0 2px 10px rgba(0,0,0,.25);display:flex;align-items:center;justify-content:center;text-align:center;z-index:5}
.brand-name{font-family:"Jost",sans-serif;font-weight:500;color:var(--pink);font-size:19px;line-height:1.15}
.main-nav{position:absolute;top:32px;left:380px;display:flex;align-items:center;font-size:16px;color:#444;text-transform:uppercase}
.main-nav a{text-decoration:none;color:inherit;margin-right:30px}
.main-nav .is-current{color:var(--pink);border:1.5px solid var(--pink);border-radius:18px;padding:5px 16px}
.cart-button{position:absolute;left:995px;top:30px;width:115px;height:36px;border-radius:18px;background:var(--blue);color:var(--white);font-size:14px;display:flex;align-items:center;justify-content:center;gap:6px}

/* hero */
.hero{position:absolute;left:0;top:92px;width:1200px;height:530px;background:linear-gradient(90deg,#e9ebe8 0%,#dfe2dc 40%,#c9c6bd 70%,#b9b4a6 100%)}
.hero-copy{position:absolute;left:88px;top:244px;color:var(--ink)}
.hero-title{font-size:19.5px;line-height:26px;color:#222}
.hero-sub{font-family:"Jost",sans-serif;text-transform:uppercase;color:var(--pink);font-size:19.8px;line-height:28px;margin-top:4px}
.hero-list{list-style:none;margin-top:8px;font-size:16px;color:#333}
.hero-list li{display:flex;align-items:center;gap:10px;height:29.5px}
.cta-button{display:flex;align-items:center;justify-content:center;width:172px;height:36px;margin-top:19px;border-radius:18px;background:var(--blue);color:var(--white);font-size:13px;text-transform:uppercase}
.slider-arrows{position:absolute;left:92px;top:506px;display:flex;gap:6px}
.slider-arrows span{width:28px;height:28px;border-radius:50%;background:#555;display:flex;align-items:center;justify-content:center}

/* welcome */
.welcome-title{position:absolute;left:0;top:676px;width:1200px;text-align:center;color:var(--blue);font-size:31px}
.welcome-text{position:absolute;left:117px;top:728px;width:968px;text-align:center;font-size:13.5px;line-height:25px;color:#444}
.feature{position:absolute;top:819px;width:300px;text-align:center}
.feature-photo{width:180px;height:180px;margin:0 auto;border-radius:50%;border:4px solid var(--white);box-shadow:0 0 0 1px #ddd}
.feature-title{margin-top:20px;font-size:22px;color:var(--ink)}
.feature-text{width:280px;margin:10px auto 0;font-size:13px;line-height:20px;color:var(--muted)}
.read-link{display:block;margin-top:6px;font-size:14px;color:var(--pink)}

/* free tips */
.tips-band{position:absolute;left:0;top:1208px;width:1200px;height:322px;background:linear-gradient(180deg,var(--blue) 0%,#2b95c9 100%);color:var(--white);text-align:center}
.tips-title{margin-top:44px;font-size:33px}
.tips-sub{font-family:"Jost",sans-serif;font-size:25px;margin-top:4px}
.tips-note{font-size:14px;margin-top:4px}
.tips-form{position:absolute;left:217px;top:199px;display:flex;gap:16px}
.field{width:291px;height:52px;background:var(--white);color:#444;font-size:13px;text-transform:uppercase;display:flex;align-items:center;padding-left:18px}
.tips-submit{width:156px;height:52px;margin-left:-6px;background:var(--pink);font-size:14px;text-transform:uppercase;display:flex;align-items:center;justify-content:center;font-weight:600}

/* program */
.program-title{position:absolute;left:88px;top:1610px;font-size:28px;color:var(--ink)}
.program-list{position:absolute;left:88px;top:1657px;list-style:none;font-size:13.5px;color:#444}
.program-list li{height:22.5px;display:flex;align-items:center;gap:8px}
.program-list li::before{content:"»";color:#666}
.outline-button{position:absolute;left:90px;top:1831px;width:100px;height:34px;border:1.5px solid var(--pink);border-radius:17px;color:var(--pink);font-size:11px;text-transform:uppercase;display:flex;align-items:center;justify-content:center}
.video-frame{position:absolute;left:624px;top:1583px;width:486px;height:309px;background:var(--white);border:1px solid #ddd;padding:7px}
.video-still{position:relative;width:100%;height:100%;background:linear-gradient(160deg,#5a4a45 0%,#3e3434 45%,#34315e 100%)}
.play{position:absolute;left:50%;top:50%;width:64px;height:64px;margin:-32px 0 0 -32px;border-radius:50%;background:rgba(0,0,0,.55);display:flex;align-items:center;justify-content:center}

/* testimonial */
.testimonial{position:absolute;left:0;top:1939px;width:1200px;height:276px;background:linear-gradient(90deg,#141416 0%,#2a2a2e 55%,#1b1b1d 100%)}
.avatar{position:absolute;left:135px;top:53px;width:160px;height:160px;border-radius:50%;border:4px solid var(--white);background:linear-gradient(180deg,#e8d3b0,#c9a684)}
.quote-badge{position:absolute;left:130px;top:46px;width:56px;height:56px;border-radius:50%;background:var(--pink);display:flex;align-items:center;justify-content:center;color:var(--white);font-family:Georgia,serif;font-size:40px;line-height:1;padding-top:14px}
.quote-text{position:absolute;left:319px;top:63px;width:775px;font-size:14.5px;line-height:24px;color:#eee}
.quote-name{position:absolute;left:323px;top:176px;font-size:15px;line-height:24px;color:#ddd}

/* news */
.news-title{position:absolute;left:0;top:2260px;width:1200px;text-align:center;font-size:27px;color:#1d3b5c}
.news-card{position:absolute;top:2326px;width:311px;text-align:center}
.news-photo{width:311px;height:198px}
.news-name{font-family:"Jost",sans-serif;font-weight:400;font-size:17px;color:#222;margin-top:14px}
.news-date{font-size:13px;color:#444;margin-top:4px}

/* footer */
.site-footer{position:absolute;left:0;top:2640px;width:1200px;height:292px;background:var(--footer)}
.footer-brand{position:absolute;left:88px;top:58px;width:128px;height:118px;display:flex;align-items:center;justify-content:center;text-align:center}
.footer-col{position:absolute;top:58px}
.footer-heading{font-size:14px;font-weight:400;color:#333;text-transform:uppercase}
.footer-lines{margin-top:16px;font-size:11.5px;line-height:24px;color:#666}
.signup{display:flex;margin-top:12px}
.signup-input{width:144px;height:32px;background:var(--white);border:1px solid #ddd;font-size:11.5px;color:#888;display:flex;align-items:center;padding-left:8px}
.signup-button{width:57px;height:32px;background:var(--pink);color:var(--white);font-size:12px;display:flex;align-items:center;justify-content:center}
.social{display:flex;gap:10px;margin-top:20px}
.social span{width:24px;height:24px;background:#555;border-radius:3px}
.footer-rule{position:absolute;left:94px;top:224px;width:1014px;height:1px;background:#ccc}
.copyright{position:absolute;left:0;top:247px;width:1200px;text-align:center;font-size:12px;color:#444}
</style>
</head>
<body>

<header class="site-header">
  <div class="brand-badge"><span class="brand-name">Tidewell<br>Mamas</span></div>
  <nav class="main-nav">
    <a class="is-current">Home</a>
    <a>About us</a>
    <a>Program</a>
    <a>Blog</a>
    <a>Shop</a>
    <a>Contact us</a>
  </nav>
  <div class="cart-button">
    <svg width="15" height="13" viewBox="0 0 15 13"><path d="M0 1h3l2 7h8l2-6H4" fill="none" stroke="#fff" stroke-width="1.6"/><circle cx="6" cy="11.5" r="1.3" fill="#fff"/><circle cx="12" cy="11.5" r="1.3" fill="#fff"/></svg>
    My cart
  </div>
</header>

<section class="hero" role="img" aria-label="Smiling mum exercising with dumbbells while her toddler reaches for them"></section>
<div class="hero-copy">
  <p class="hero-title">Lose your baby weight and get back into great shape!</p>
  <p class="hero-sub">12 week home workout program for mums!</p>
  <ul class="hero-list">
    <li><svg width="14" height="12" viewBox="0 0 14 12"><path d="M1 6l4 4 8-9" fill="none" stroke="#d6187a" stroke-width="2.4"/></svg>12 week, cardio and resistance circuit training program</li>
    <li><svg width="14" height="12" viewBox="0 0 14 12"><path d="M1 6l4 4 8-9" fill="none" stroke="#d6187a" stroke-width="2.4"/></svg>Workout equipment delivered to your front door</li>
    <li><svg width="14" height="12" viewBox="0 0 14 12"><path d="M1 6l4 4 8-9" fill="none" stroke="#d6187a" stroke-width="2.4"/></svg>Accountability charts &amp; program cards</li>
    <li><svg width="14" height="12" viewBox="0 0 14 12"><path d="M1 6l4 4 8-9" fill="none" stroke="#d6187a" stroke-width="2.4"/></svg>Family friendly healthy recipes</li>
  </ul>
  <div class="cta-button">Get started now!</div>
</div>
<div class="slider-arrows">
  <span><svg width="10" height="12" viewBox="0 0 10 12"><path d="M7 1L2 6l5 5" fill="none" stroke="#fff" stroke-width="2"/></svg></span>
  <span><svg width="10" height="12" viewBox="0 0 10 12"><path d="M3 1l5 5-5 5" fill="none" stroke="#fff" stroke-width="2"/></svg></span>
</div>

<h2 class="welcome-title heading">Welcome to Tidewell Mamas</h2>
<p class="welcome-text">After a life time of competitive sports and as a qualified personal trainer, I thought I knew exactly what it would take to get my body back after having babies. I put on a massive 30 kgs with my first pregnancy and found myself in a situation for the first time in my life where I had to lose a lot of weight.</p>

<article class="feature" style="left:108px">
  <div class="feature-photo" role="img" aria-label="Mum doing sit-ups on a mat" style="background:linear-gradient(160deg,#6b3a3a,#2d2f4d)"></div>
  <h3 class="feature-title heading">Workout program</h3>
  <p class="feature-text">This sparked a huge determination and curiosity within me and I spent the next 2 years studying and researching</p>
  <span class="read-link">Read More -&gt;</span>
</article>
<article class="feature" style="left:452px">
  <div class="feature-photo" role="img" aria-label="Trainer portrait in a green top" style="background:linear-gradient(180deg,#b9906e,#c8d86a)"></div>
  <h3 class="feature-title heading">Training program</h3>
  <p class="feature-text">This sparked a huge determination and curiosity within me and I spent the next 2 years studying and researching</p>
  <span class="read-link">Read More -&gt;</span>
</article>
<article class="feature" style="left:794px">
  <div class="feature-photo" role="img" aria-label="Trainer lifting dumbbells at home" style="background:linear-gradient(160deg,#8e2b2b,#3a3d6a)"></div>
  <h3 class="feature-title heading">Healthy recipes</h3>
  <p class="feature-text">This sparked a huge determination and curiosity within me and I spent the next 2 years studying and researching</p>
  <span class="read-link">Read More -&gt;</span>
</article>

<section class="tips-band" aria-label="Free tips sign-up">
  <h2 class="tips-title heading">Get your free top 10</h2>
  <p class="tips-sub">Baby Belly Blasting Tips</p>
  <p class="tips-note">See our secret tips to a flatter yummy mummy tummy that you can start implementing</p>
  <div class="tips-form">
    <div class="field">Name</div>
    <div class="field">Email ID</div>
    <div class="tips-submit">Get it free now!</div>
  </div>
</section>

<h2 class="program-title heading">What's included in the program?</h2>
<ul class="program-list">
  <li>Our unique 3 stage, 12 week training program</li>
  <li>Full Instructional Workout DVD and program cards for each program</li>
  <li>Weekly accountability charts</li>
  <li>Weekly coaching emails</li>
  <li>Funky exercise equipment for your home</li>
  <li>Nutritionist approved healthy eating guide</li>
  <li>Healthy Family Favourites recipe ebook</li>
</ul>
<div class="outline-button">Read more »</div>
<div class="video-frame">
  <div class="video-still" role="img" aria-label="Video still of a mum exercising on a step beside her baby in a living room">
    <div class="play"><svg width="22" height="24" viewBox="0 0 22 24"><path d="M3 2l17 10L3 22z" fill="#fff"/></svg></div>
  </div>
</div>

<section class="testimonial" aria-label="Testimonial">
  <div class="avatar" role="img" aria-label="Portrait of the founder"></div>
  <div class="quote-badge">“</div>
  <p class="quote-text">It has survived not only five centuries, but also the leap into electronic typesetting, remaining essentially unchanged. It was popularised in the 1960s with the release of Pressmark sheets containing Lorem Ipsum passages, and more recently with desktop publishing software like Quillset Composer including versions of Lorem Ipsum t has survived not only five centuries, but also the leap into electronic typesetting,</p>
  <p class="quote-name">Porro quisquam<br>Founder, dolorem ipsum</p>
</section>

<h2 class="news-title heading">Latest news</h2>
<article class="news-card" style="left:94px">
  <div class="news-photo" role="img" aria-label="Trainer doing a side plank in a living room" style="background:linear-gradient(170deg,#c9c4bd,#3b3b3f 70%,#4a3f6a)"></div>
  <h3 class="news-name">Neque porro quisquam est qui</h3>
  <p class="news-date">19/05/17</p>
</article>
<article class="news-card" style="left:446px">
  <div class="news-photo" role="img" aria-label="Mum exercising on a rug with her child" style="background:linear-gradient(170deg,#9b3a3a,#3a3a3c 60%,#6e6e72)"></div>
  <h3 class="news-name">Dolorem ipsum quia dolor sit amet</h3>
  <p class="news-date">17/05/17</p>
</article>
<article class="news-card" style="left:796px">
  <div class="news-photo" role="img" aria-label="Trainer in a bright green top lifting a dumbbell" style="background:linear-gradient(170deg,#8e2d2d,#2f3033 55%,#7cc24a)"></div>
  <h3 class="news-name">Quisquam est qui dolorem</h3>
  <p class="news-date">13/05/17</p>
</article>

<footer class="site-footer">
  <div class="footer-brand"><span class="brand-name">Tidewell<br>Mamas</span></div>
  <div class="footer-col" style="left:332px">
    <h4 class="footer-heading">Contact us</h4>
    <p class="footer-lines">Address : 12 Harlow Lane, Eastgate<br>Porthmere, Pm4 7QX<br>Phone : 555-013-7742.<br>Email : hello@tidewellmamas.com.au</p>
  </div>
  <div class="footer-col" style="left:618px">
    <h4 class="footer-heading">Join our mailing list</h4>
    <p class="footer-lines" style="margin-top:12px;line-height:16px;width:200px">Your about us information would fit here nicely.</p>
    <div class="signup"><div class="signup-input">Email address</div><div class="signup-button">Submit</div></div>
  </div>
  <div class="footer-col" style="left:936px">
    <h4 class="footer-heading">Follow us out there</h4>
    <div class="social" aria-label="Social links"><span></span><span></span><span></span><span></span></div>
  </div>
  <div class="footer-rule"></div>
  <p class="copyright">Copyright © 2017. All Rights Reserved</p>
</footer>

</body>
</html>
```